STICKER DESIGN required for packaging. UK START UP TEA BUSINESS

We are looking for a design for a sticker that will be applied to packaging for our teas! We are a new start up Tea business based in the UK called 'BrookLeafs'
Selling quality loose leaf tea and teabags via our online shop and also face to face at farmers markets / food shows and eventually in our own tea emporium. We will be marketing our teas to hotels, cafes, delis etc. too
We carry every day teas eg. breakfast blends and also speciality and rare teas to offer customers the chance to try something new. Tea as a treat / ritual / indulgence / healthy lifestyle choice / modern
The design will initially be printed on vinyl stickers and then applied to the tea packaging (pouch bags in matte black and matte silver), in the future the design may be printed direct onto our packaging. The sticker design will need to be scalable as the size of the pouch bag varies dependant on the tea.
The sticker we have in mind is a leaf shape (sketch attached)
colour green to match our logo
It will include our logo (files attached)
Text to be included on the sticker is
- www.brookleafs.co.uk
- Welmoor, England
- The tea type eg. Green
It will need to complement both black and silver pouches that we are using to package our teas (see attached image of our pouches)
Colours - green leaf, see our corporate colours (green & orange) on our logo files attached. We also like silver and black.
Font - nothing to swirly, must be easy to read on the packaging
once a sticker design is agreed for the initial tea type (Green) we will require additional files for each tea type that we stock. Just the tea type (Green) to be updated - the rest of the design to stay the same. The tea types we stock are listed below
Green
Black
Oolong
White
Herbal
Blended
Happy to answer any questions and aim to give feedback daily! Thank you for your interest
Best regards

```html
<!DOCTYPE html>
<html lang="en">
<head>
<meta charset="utf-8">
<title>BrookLeafs – Green Tea Sticker</title>
<link rel="stylesheet" href="https://fonts.googleapis.com/css2?family=Nunito+Sans:wght@300;400;600&display=swap">
<style>
  :root {
    --leaf-green: #066a3a;
    --brand-orange: #f08a1c;
    --tea-green: #7cc142;
    --backdrop-light: #ffffff;
    --backdrop-dark: #9c9c9c;
  }
  html, body {
    margin: 0;
    padding: 0;
    width: 1200px;
    height: 1000px;
    overflow: hidden;
  }
  .canvas {
    position: relative;
    width: 1200px;
    height: 1000px;
    background: radial-gradient(ellipse 560px 470px at 50% 50%, var(--backdrop-light) 72%, #e6e6e6 86%, var(--backdrop-dark) 130%);
    font-family: "Nunito Sans", sans-serif;
  }
  .sticker {
    position: absolute;
    inset: 0;
    width: 1200px;
    height: 1000px;
  }
  .leaf-shape { fill: var(--leaf-green); }
  .leaf-web {
    fill: var(--brand-orange);
    font-size: 17px;
    font-weight: 400;
    letter-spacing: 2.2px;
  }
  .leaf-place {
    fill: var(--brand-orange);
    font-size: 17px;
    font-weight: 400;
    letter-spacing: 1.6px;
  }
  .brand-name {
    fill: var(--brand-orange);
    font-size: 42px;
    font-weight: 400;
    letter-spacing: 0.5px;
  }
  .tea-type {
    fill: var(--tea-green);
    font-size: 13px;
    font-weight: 400;
    letter-spacing: 5px;
  }
</style>
</head>
<body>
  <main class="canvas">
    <svg class="sticker" viewBox="0 0 1200 1000" xmlns="http://www.w3.org/2000/svg" aria-label="BrookLeafs green tea leaf sticker">
      <path class="leaf-shape" d="M903 264 C840 295 760 305 660 318 C560 332 470 355 420 420 C370 490 340 590 335 700 C332 770 338 815 345 835 C348 848 364 848 362 832 C356 800 352 760 362 745 C385 715 420 700 470 690 C560 675 630 668 690 640 C790 590 850 500 880 410 L915 282 C920 265 912 258 903 264 Z"/>
      <text class="leaf-web" x="652" y="345" transform="rotate(-10 652 345)">www.brookleafs.co.uk</text>
      <text class="brand-name" x="596" y="538" text-anchor="middle">BrookLeafs</text>
      <text class="tea-type" x="598" y="579" text-anchor="middle">GREEN</text>
      <text class="leaf-place" x="396" y="707" transform="rotate(-12 396 707)">Welmoor, England</text>
    </svg>
  </main>
</body>
</html>
```